SaaS Early tech startup business card design

Unique design for experience ecommerce platform company. the business cards will be used by executive members. conformance with color code is required.

```html
<!DOCTYPE html>
<html lang="en">
<head>
<meta charset="utf-8">
<title>Kelvra Business Card</title>
<link href="https://fonts.googleapis.com/css2?family=Poppins:wght@400;500;700&display=swap" rel="stylesheet">
<style>
  :root {
    --stage: #2a2a2e;
    --card: #23213a;
    --card-edge: #2c2a47;
    --teal: #2bbf9f;
    --blue: #137aa0;
    --ink: #f2f2f5;
    --icon-glyph: #1c2a33;
  }
  * { margin: 0; padding: 0; box-sizing: border-box; }
  html, body {
    width: 1200px; height: 900px; overflow: hidden;
    background: var(--stage);
    font-family: "Poppins", Arial, sans-serif;
  }
  .canvas { position: relative; width: 1200px; height: 900px; }
  .card {
    position: absolute; left: 270px;
    width: 660px; height: 377px;
    background: linear-gradient(135deg, var(--card) 60%, var(--card-edge));
    border-radius: 22px; overflow: hidden;
    box-shadow: 0 14px 30px rgba(0,0,0,.45);
  }
  .card-front { top: 48px; }
  .card-back { top: 475px; }

  .wordmark {
    position: absolute; color: var(--teal);
    font-weight: 700; letter-spacing: 1px; line-height: 1;
  }
  .card-front .wordmark { left: 60px; top: 140px; font-size: 78px; }
  .front-decoration {
    position: absolute; right: 60px; top: 70px;
    width: 220px; height: 200px; border-radius: 40px;
    background: radial-gradient(circle, rgba(43,191,159,.10), rgba(19,122,160,.04) 60%, transparent 75%);
  }

  .name-bar {
    position: absolute; left: 0; top: 44px;
    width: 8px; height: 62px; background: var(--teal);
  }
  .person { position: absolute; left: 34px; top: 40px; }
  .person-name { color: var(--teal); font-weight: 700; font-size: 26px; line-height: 1.2; }
  .person-role { color: var(--ink); font-size: 16px; font-weight: 400; }
  .card-back .wordmark { right: 42px; top: 40px; font-size: 66px; }

  .divider { position: absolute; left: 0; top: 190px; width: 660px; height: 16px; }

  .address {
    position: absolute; right: 42px; top: 222px;
    color: var(--ink); font-size: 16px; text-align: right; line-height: 1.35;
  }
  .contacts { position: absolute; left: 40px; top: 262px; list-style: none; }
  .contact {
    display: flex; align-items: center; gap: 12px;
    color: var(--ink); font-size: 19px; height: 30px;
  }
  .contact-icon { width: 22px; height: 22px; flex: none; }
</style>
</head>
<body>
<main class="canvas">
  <section class="card card-front">
    <span class="wordmark">Kelvra</span>
    <div class="front-decoration" role="img" aria-label="Faint decorative line pattern"></div>
  </section>

  <section class="card card-back">
    <span class="name-bar"></span>
    <div class="person">
      <p class="person-name">Daniel Reyes</p>
      <p class="person-role">Manager</p>
    </div>
    <span class="wordmark">Kelvra</span>

    <svg class="divider" viewBox="0 0 660 16" aria-hidden="true">
      <rect x="0" y="2" width="340" height="3" fill="var(--blue)"/>
      <rect x="0" y="10" width="340" height="3" fill="var(--blue)"/>
      <rect x="340" y="2" width="320" height="3" fill="var(--teal)"/>
      <rect x="340" y="10" width="320" height="3" fill="var(--teal)"/>
    </svg>

    <p class="address">48 Harbor Lane, Fairview<br>Oregon, 97001</p>

    <ul class="contacts">
      <li class="contact">
        <svg class="contact-icon" viewBox="0 0 22 22" aria-hidden="true">
          <rect width="22" height="22" rx="5" fill="var(--teal)"/>
          <path d="M7 5c1 0 2 2 2 3s-1 1-1 2 2 3 3 3 1-1 2-1 3 1 3 2-1 3-3 3C9 17 5 13 5 8c0-2 1-3 2-3z" fill="var(--icon-glyph)"/>
        </svg>
        <span>555-014-3827</span>
      </li>
      <li class="contact">
        <svg class="contact-icon" viewBox="0 0 22 22" aria-hidden="true">
          <rect width="22" height="22" rx="5" fill="var(--teal)"/>
          <rect x="5" y="7" width="12" height="9" fill="none" stroke="var(--icon-glyph)" stroke-width="1.6"/>
          <path d="M5 7l6 5 6-5" fill="none" stroke="var(--icon-glyph)" stroke-width="1.6"/>
        </svg>
        <span>daniel@kelvra-mail.com</span>
      </li>
      <li class="contact">
        <svg class="contact-icon" viewBox="0 0 22 22" aria-hidden="true">
          <rect width="22" height="22" rx="5" fill="var(--teal)"/>
          <circle cx="11" cy="11" r="6" fill="none" stroke="var(--icon-glyph)" stroke-width="1.5"/>
          <ellipse cx="11" cy="11" rx="2.6" ry="6" fill="none" stroke="var(--icon-glyph)" stroke-width="1.3"/>
          <path d="M5 11h12" stroke="var(--icon-glyph)" stroke-width="1.3"/>
        </svg>
        <span>www.kelvra-demo.com</span>
      </li>
    </ul>
  </section>
</main>
</body>
</html>
```